Bow Tie Post Card (Post Card to Package a Children's Bow Tie)

Bowties have been added to our company's inventory and we want to print postcards to package and fasten them to (please see images for an example).

Please use the attached photos for reference. I would like to use the head portion of our logo and remove the tie to leave a spot for an actual tie. I want something fun and clever to look at. Something that is thoughtful cute when people open it. Maybe a fun patterned background or a boarder? It could say The Kite Nest or www.thekitenest.com on there somewhere if there is space or seems right but does not have to.

The post cards are 4x6 inches. The bow ties themselves are about 3.5x2 inches.

Thank you.

Target Market(s)

Children's clothing and accessories.

Industry/Entity Type

It Company

Font styles to use
Sans Serif

Requirements
Must have
• Must use the same coloring of the brand. Please see the website for reference. These are the color colors used:
• 86CFC6
• 568686
• F3F2F0
• 757575
• CF1313
• *other colors may be used but these are the general brand colors.
• Font: Century Gothic Regular and Black Larch
Nice to have
• Should be nice, clean, modern and fun.

```html
<!DOCTYPE html>
<html lang="en">
<head>
<meta charset="utf-8">
<title>The Kite Nest – Bow Tie Post Card</title>
<link href="https://fonts.googleapis.com/css2?family=Questrial&display=swap" rel="stylesheet">
<style>
  :root {
    --teal: #86cfc6;
    --sky: #b2e2ea;
    --cream: #f3f2f0;
    --grey: #757575;
    --red: #cf1313;
    --backdrop: #e4e4e2;
  }
  html, body {
    margin: 0;
    padding: 0;
    width: 1200px;
    height: 979px;
    overflow: hidden;
    background: var(--backdrop);
  }
  .canvas {
    position: relative;
    width: 1200px;
    height: 979px;
    font-family: "Questrial", sans-serif;
  }
  .card {
    position: absolute;
    width: 474px;
    height: 710px;
    background: repeating-linear-gradient(
      to bottom,
      var(--teal) 0 22px,
      var(--sky) 22px 32px
    );
    box-shadow: 4px 6px 14px rgba(0, 0, 0, 0.28);
    overflow: hidden;
  }
  .card--front { left: 61px; top: 118px; }
  .card--back  { left: 648px; top: 153px; }

  .panel-shape { position: absolute; display: block; }
  .panel-shape path { fill: var(--cream); }

  .front-panel { left: 32px; top: 61px; width: 416px; height: 586px; }
  .back-label  { left: 91px; top: 496px; width: 303px; height: 140px; }

  .bow-tie-spot {
    position: absolute;
    left: 92px;
    top: 74px;
    width: 294px;
    height: 402px;
    border-radius: 18px;
    background: linear-gradient(180deg, #bfe6e1 0%, #bfe6e1 68%, #e9b3b3 100%);
  }

  .wordmark {
    position: absolute;
    left: 0;
    width: 100%;
    margin: 0;
    text-align: center;
    color: var(--teal);
    font-weight: 400;
    letter-spacing: -0.5px;
    line-height: 1;
  }
  .wordmark--front { top: 552px; font-size: 42px; }
  .wordmark--back  { top: 533px; font-size: 34px; }

  .web-address {
    position: absolute;
    left: 0;
    top: 598px;
    width: 100%;
    margin: 0;
    text-align: center;
    color: var(--grey);
    font-size: 17px;
    letter-spacing: 0.3px;
  }
</style>
</head>
<body>
<div class="canvas">

  <section class="card card--front">
    <svg class="panel-shape front-panel" viewBox="0 0 416 586" width="416" height="586" aria-hidden="true">
      <path d="M48 0 H368 A48 48 0 0 0 416 48 V538 A48 48 0 0 0 368 586 H48 A48 48 0 0 0 0 538 V48 A48 48 0 0 0 48 0 Z"/>
    </svg>
    <div class="bow-tie-spot" role="img" aria-label="Illustration area: outlined child's head in teal above a red bow tie"></div>
    <p class="wordmark wordmark--front">The Kite Nest</p>
  </section>

  <section class="card card--back">
    <svg class="panel-shape back-label" viewBox="0 0 303 140" width="303" height="140" aria-hidden="true">
      <path d="M22 0 H281 A22 22 0 0 0 303 22 V118 A22 22 0 0 0 281 140 H22 A22 22 0 0 0 0 118 V22 A22 22 0 0 0 22 0 Z"/>
    </svg>
    <p class="wordmark wordmark--back">The Kite Nest</p>
    <p class="web-address">www.thekitenest.com</p>
  </section>

</div>
</body>
</html>
```